Store Promo Card (already have logo!)

I need a card design (single side) for my online women’s gift shop containing a promotional code to be placed in bags for attendees at an event. I’m flexible on both shape and sizing, but perhaps a 4x6 card.
—It should contain my attached logo, my website (www.brivelhome.com), and my Instagram handle (@brivelhome) and promotion language such as “15% off your purchase with code: PELVON”.
—I think I would like my logo to be large.
—It should be clean, simple and modern in design and should use the colors from my logo.
—I would like about 3-5 product pictures depending on design.
Target Market(s)
Women ages 30 to 60
Industry/Entity Type
Retail Upscale Gift

```html
<!DOCTYPE html>
<html lang="en">
<head>
<meta charset="utf-8">
<title>Brivel Promo Card</title>
<link rel="stylesheet" href="https://fonts.googleapis.com/css2?family=Abril+Fatface&family=EB+Garamond:wght@500;600&display=swap">
<style>
  :root {
    --backdrop: #ece3d8;
    --card-white: #f7f6f4;
    --blush: #f2c9c0;
    --ink: #474b4d;
  }
  * { margin: 0; padding: 0; box-sizing: border-box; }
  html, body {
    width: 1200px;
    height: 800px;
    overflow: hidden;
    background: var(--backdrop);
  }
  .promo-card {
    position: absolute;
    left: 100px;
    top: 120px;
    width: 1000px;
    height: 560px;
    background: var(--card-white);
    padding: 22px;
    box-shadow: 0 6px 18px rgba(90, 70, 50, 0.18);
  }
  .card-panel {
    position: relative;
    width: 956px;
    height: 516px;
    background: var(--blush);
    color: var(--ink);
  }
  .frame-lines {
    position: absolute;
    inset: 0;
  }
  .frame-lines path {
    fill: none;
    stroke: var(--ink);
    stroke-width: 2.5;
  }
  .brand-name {
    position: absolute;
    left: 40px;
    top: 50px;
    width: 390px;
    height: 200px;
    display: flex;
    align-items: center;
    justify-content: center;
    font-family: "Abril Fatface", serif;
    font-size: 92px;
    letter-spacing: 2px;
  }
  .website {
    position: absolute;
    left: 70px;
    top: 335px;
    width: 400px;
    text-align: center;
    font-family: "EB Garamond", serif;
    font-weight: 600;
    font-size: 40px;
    line-height: 1;
  }
  .social-handle {
    position: absolute;
    left: 150px;
    top: 450px;
    width: 240px;
    height: 40px;
    display: flex;
    align-items: center;
    justify-content: center;
    gap: 12px;
    font-family: "EB Garamond", serif;
    font-weight: 600;
    font-size: 32px;
  }
  .social-dot {
    width: 24px;
    height: 24px;
    border: 2.5px solid var(--ink);
    border-radius: 50%;
  }
  .offer-amount {
    position: absolute;
    left: 510px;
    top: 70px;
    width: 405px;
    text-align: center;
    font-family: "Abril Fatface", serif;
    font-size: 132px;
    line-height: 0.98;
  }
  .offer-terms {
    position: absolute;
    left: 510px;
    top: 382px;
    width: 405px;
    text-align: center;
    font-family: "EB Garamond", serif;
    font-weight: 600;
    font-size: 26px;
    line-height: 1;
  }
  .promo-code {
    position: absolute;
    left: 595px;
    top: 446px;
    width: 240px;
    text-align: center;
    font-family: "EB Garamond", serif;
    font-weight: 600;
    font-size: 44px;
    line-height: 1;
    letter-spacing: 1px;
  }
</style>
</head>
<body>
  <article class="promo-card">
    <div class="card-panel">
      <svg class="frame-lines" width="956" height="516" viewBox="0 0 956 516" aria-hidden="true">
        <path class="brand-frame" d="M40 50 H430 V250 H40 Z"/>
        <path class="contact-frame" d="M150 470 H70 V285 H470 V470 H390"/>
        <path class="offer-frame" d="M595 470 H510 V30 H915 V470 H835"/>
      </svg>

      <div class="brand-name">BRIVEL</div>

      <div class="website">www.brivelhome.com</div>
      <div class="social-handle">
        <span class="social-dot"></span>
        <span>@brivelhome</span>
      </div>

      <div class="offer-amount">15%<br>OFF</div>
      <div class="offer-terms">your purchase with code:</div>
      <div class="promo-code">PELVON</div>
    </div>
  </article>
</body>
</html>
```